We need a new business card that reflects who we are. Professional, classy, modern, and service ori

We need a business card design for a window coverings design company in Kansas City called Bright Lane Interiors. We offer professional, modern, and high quality window covering products. We are looking to portray an image of a big, national franchise. We are a 5 location (with showrooms) business with 10 professional designers and 4 professional installers. These cards will be used with Thank you cards, given to realtors, and asked for referrals with.

Target Market(s)

Kansas City

Industry/Entity Type

Business

Contact Information for Business Card

We would like our card to look clean and simple on the front, featuring our logo and Marlow Fenwick's. Our designers' phone numbers and emails should be displayed as well as their title.

Font styles to use
Sans Serif

Colors

Designer to choose colors to be used in the design.

Requirements
Must have
• Front - Logos, name, phone number, email address
• Back - Showroom locations, social media? Appt date/time?
Nice to have
• I would like a clean and modern look (not contemporary. I like a white background, but I am open to ideas. Looking for a "National chain" look for a small business.
Should not have
• Too much busyness.

```html
<!DOCTYPE html>
<html lang="en">
<head>
<meta charset="utf-8">
<title>Bright Lane Interiors – Business Card</title>
<link rel="stylesheet" href="https://fonts.googleapis.com/css2?family=Lato:wght@400;700&family=Tinos:wght@400;700&display=swap">
<style>
  :root {
    --stage: #666666;
    --card: #ffffff;
    --brand-red: #c8414a;
    --brand-grey: #8e9296;
    --ink: #1a1a1a;
    --ink-soft: #3a3a3a;
    --partner-ink: #4a4f55;
    --serif: "Tinos", "Times New Roman", serif;
    --sans: "Lato", "Helvetica Neue", Arial, sans-serif;
  }
  * { box-sizing: border-box; margin: 0; padding: 0; }
  html, body { width: 1200px; height: 900px; overflow: hidden; }
  body { background: var(--stage); position: relative; font-family: var(--sans); }

  .card {
    position: absolute;
    top: 306px;
    width: 439px;
    height: 272px;
    background: var(--card);
    box-shadow: 2px 3px 5px rgba(0,0,0,0.45);
    overflow: hidden;
  }
  .card--front { left: 150px; }
  .card--back  { left: 609px; }

  /* Front */
  .front__corner { position: absolute; left: 0; top: 26px; }
  .front__person { position: absolute; left: 36px; top: 32px; }
  .person__name {
    font-family: var(--serif); font-weight: 700; font-size: 15.5px;
    letter-spacing: 0.3px; color: var(--ink); line-height: 1;
  }
  .person__first { color: var(--brand-red); }
  .person__title { font-size: 12.5px; color: var(--ink); margin-top: 2px; line-height: 1.2; }

  .front__brand {
    position: absolute; left: 220px; top: 120px; width: 200px; text-align: center;
  }
  .brand__name {
    font-family: var(--serif); font-size: 19px; color: var(--ink); white-space: nowrap;
  }
  .brand__tagline {
    font-family: var(--serif); font-size: 10.5px; color: var(--ink); margin-top: 3px; white-space: nowrap;
  }

  .front__contact { position: absolute; left: 25px; top: 207px; font-size: 12.5px; color: var(--ink); }
  .contact__row { display: flex; align-items: center; gap: 4px; height: 16px; }
  .contact__icon { width: 10px; height: 10px; flex: none; }

  .front__partner {
    position: absolute; right: 22px; top: 216px;
    font-size: 13px; font-weight: 700; color: var(--partner-ink); white-space: nowrap;
  }

  .front__stripes { position: absolute; left: 0; bottom: 0; }

  /* Back */
  .back__header {
    height: 75px; background: var(--brand-red); display: flex; align-items: center; justify-content: center;
  }
  .back__title { font-family: var(--serif); font-size: 28px; color: #fff; letter-spacing: 0.3px; }
  .back__appointment { position: relative; height: 116px; }
  .appointment__field {
    position: absolute; left: 105px; font-size: 13px; color: var(--ink); white-space: nowrap;
  }
  .appointment__field--date { top: 33px; }
  .appointment__field--time { top: 64px; }
  .appointment__line { display: inline-block; width: 192px; border-bottom: 1px solid var(--ink-soft); margin-left: 1px; }
  .appointment__field--time .appointment__line { width: 194px; }

  .back__locations {
    height: 81px; background: var(--brand-grey); color: #fff; text-align: center; padding-top: 17px;
  }
  .locations__heading { font-size: 12.5px; letter-spacing: 0.2px; }
  .locations__list {
    list-style: none; display: flex; justify-content: center; align-items: center;
    margin-top: 16px; font-size: 12.5px; white-space: nowrap;
  }
  .locations__list li + li::before {
    content: ""; display: inline-block; width: 6px; height: 6px; border-radius: 50%;
    background: #fff; margin: 0 6px 1px 6px; vertical-align: middle;
  }
</style>
</head>
<body>

<section class="card card--front" aria-label="Business card front">
  <svg class="front__corner" width="30" height="37" viewBox="0 0 30 37" aria-hidden="true">
    <polygon points="0,0 13,0 15,37 0,37" fill="var(--brand-grey)"/>
    <polygon points="13,0 28,0 28,37 15,37" fill="var(--brand-red)"/>
  </svg>

  <div class="front__person">
    <p class="person__name"><span class="person__first">DANIEL</span> HARPER</p>
    <p class="person__title">Managing Director</p>
  </div>

  <div class="front__brand">
    <p class="brand__name">Bright Lane Interiors</p>
    <p class="brand__tagline">Blinds, Shades, Shutters, Draperies &amp; Decor</p>
  </div>

  <div class="front__contact">
    <p class="contact__row">
      <svg class="contact__icon" viewBox="0 0 10 10" aria-hidden="true">
        <path d="M1 3.5 Q5 0.5 9 3.5 L8 5 L6.5 4 L6.5 3.2 Q5 2.6 3.5 3.2 L3.5 4 L2 5 Z" fill="var(--brand-red)"/>
        <rect x="2" y="5.5" width="6" height="3.5" rx="0.6" fill="var(--brand-red)"/>
      </svg>
      816 555 0142
    </p>
    <p class="contact__row">
      <svg class="contact__icon" viewBox="0 0 10 10" aria-hidden="true">
        <rect x="0.5" y="2" width="9" height="6.5" fill="var(--brand-red)"/>
        <polyline points="0.8,2.4 5,5.8 9.2,2.4" fill="none" stroke="#fff" stroke-width="0.9"/>
      </svg>
      info@brightlane.com
    </p>
  </div>

  <p class="front__partner">Marlow Fenwick Gallery</p>

  <svg class="front__stripes" width="439" height="20" viewBox="0 0 439 20" aria-hidden="true">
    <rect x="0" y="6" width="222" height="14" fill="var(--brand-grey)"/>
    <polygon points="207,20 222,2 439,2 439,20" fill="var(--brand-red)"/>
  </svg>
</section>

<section class="card card--back" aria-label="Business card back">
  <header class="back__header">
    <p class="back__title">Bright Lane Interiors</p>
  </header>

  <div class="back__appointment">
    <p class="appointment__field appointment__field--date">DATE<span class="appointment__line"></span></p>
    <p class="appointment__field appointment__field--time">TIME<span class="appointment__line"></span></p>
  </div>

  <footer class="back__locations">
    <p class="locations__heading">SHOWROOM LOCATIONS</p>
    <ul class="locations__list">
      <li>Location 1</li>
      <li>Location 2</li>
      <li>Location 3</li>
      <li>Location 4</li>
      <li>Location 5</li>
    </ul>
  </footer>
</section>

</body>
</html>
```